Company Mission & Values Poster

I'd like an A2 Portrait Poster displaying our company's Mission & Values.
See our website for our logo, fonts, mission & values.
https://valdintor.com.au/

Our Mission: Creating homes for abundant life
Values: Love, Thinking, Team, Zoe.

Some ideas to consider:
Mission as the Headline then
A logo for each of the 4 Values and the words

Target Market(s)

Myself & my team

Industry/Entity Type

Real Estate

Font styles to use
Other font styles liked:
• Company fonts as seen on our website

```html
<!DOCTYPE html>
<html lang="en">
<head>
<meta charset="utf-8">
<title>Valdintor — Mission &amp; Values</title>
<link rel="stylesheet" href="https://fonts.googleapis.com/css2?family=Gloock&family=Figtree:wght@300;500&display=swap">
<style>
  :root {
    --forest: #0a3a33;
    --card: #17625a;
    --rule: #2f9287;
    --hero-top: #3e5f4e;
    --hero-bottom: #2a4a3b;
    --paper: #f4f7f5;
    --ink: #ffffff;
    --ink-soft: #e3eeeb;
    --serif: "Gloock", "Times New Roman", serif;
    --sans: "Figtree", "Helvetica Neue", Arial, sans-serif;
  }
  * { box-sizing: border-box; margin: 0; padding: 0; }
  html, body { width: 849px; height: 1200px; overflow: hidden; background: var(--paper); }
  .poster { position: relative; width: 849px; height: 1200px; overflow: hidden; }

  .hero {
    position: absolute; left: 0; top: 0; width: 849px; height: 391px;
    background: linear-gradient(180deg, var(--hero-top) 0%, #4a6a58 45%, var(--hero-bottom) 100%);
  }
  .hero-title {
    position: absolute; left: 0; top: 108px; width: 100%;
    font-family: var(--serif); font-weight: 400; font-size: 64px; line-height: 70px;
    color: var(--ink); text-align: center; letter-spacing: 0.5px;
  }
  .hero-intro {
    position: absolute; left: 0; top: 268px; width: 100%;
    font-family: var(--sans); font-weight: 500; font-size: 17px; line-height: 25.5px;
    color: var(--ink); text-align: center;
  }

  .values {
    position: absolute; left: 0; top: 391px; width: 849px; height: 668px;
    background: var(--forest);
  }
  .values-statement {
    position: absolute; left: 0; top: 130px; width: 100%;
    font-family: var(--serif); font-weight: 400; font-size: 31px; line-height: 41px;
    color: var(--ink); text-align: center;
  }
  .value-card {
    position: absolute; top: 302px; width: 182px; height: 324px;
    background: var(--card); border-radius: 0 0 24px 24px;
  }
  .value-card:nth-of-type(1) { left: 32px; }
  .value-card:nth-of-type(2) { left: 234px; }
  .value-card:nth-of-type(3) { left: 436px; }
  .value-card:nth-of-type(4) { left: 639px; }
  .value-badge {
    position: absolute; left: 50%; top: -56px; width: 112px; height: 112px;
    margin-left: -56px; border-radius: 50%;
    background: var(--card); border: 4px solid var(--forest); border-top-color: var(--card);
    display: flex; align-items: center; justify-content: center;
  }
  .value-badge svg { width: 60px; height: 60px; fill: none; stroke: var(--ink); stroke-width: 1.6; stroke-linecap: round; stroke-linejoin: round; }
  .value-name {
    position: absolute; left: 0; top: 74px; width: 100%;
    font-family: var(--serif); font-weight: 400; font-size: 35px; line-height: 40px;
    color: var(--ink); text-align: center;
  }
  .value-rule {
    position: absolute; left: 17px; top: 118px; width: 148px; height: 1.5px; background: var(--rule);
  }
  .value-text {
    position: absolute; left: 10px; top: 126px; width: 162px;
    font-family: var(--sans); font-weight: 300; font-size: 13px; line-height: 17px;
    color: var(--ink-soft); text-align: center;
  }

  .footer {
    position: absolute; left: 0; top: 1059px; width: 849px; height: 141px;
    background: var(--paper);
    display: flex; align-items: center; justify-content: center;
  }
  .brand-name {
    font-family: var(--serif); font-weight: 400; font-size: 46px; letter-spacing: 7px;
    color: var(--forest);
  }
</style>
</head>
<body>
<main class="poster">
  <section class="hero" role="img" aria-label="Photograph of a modern multi-level home surrounded by lush tropical gardens, toned in deep green">
    <h1 class="hero-title">Creating homes for<br>abundant life</h1>
    <p class="hero-intro">We wholeheartedly believe that home is an extraordinary place:<br>A haven where life unfolds in all its glory.<br>Where we find solace, make cherished memories with loved ones,<br>and savour the&nbsp; natural beauty that surrounds us.</p>
  </section>

  <section class="values">
    <h2 class="values-statement">We believe business can be a force for good.<br>Our values shape the way we work,<br>and how we make decisions.</h2>

    <article class="value-card">
      <div class="value-badge">
        <svg viewBox="0 0 60 60" aria-hidden="true">
          <path d="M31 52 C20 43 8 35 8 23 C8 15 14 10 20 10 C25 10 29 13 31 18 C33 13 37 10 42 10 C48 10 53 15 52 23 C51 35 40 43 31 52 Z"/>
          <path d="M22 16 C14 18 13 28 20 34"/>
        </svg>
      </div>
      <h3 class="value-name">Love</h3>
      <div class="value-rule"></div>
      <p class="value-text">Our mission is founded in our love and respect for people - those we develop for, those in our teams and those in the communities we create and operate within.</p>
    </article>

    <article class="value-card">
      <div class="value-badge">
        <svg viewBox="0 0 60 60" aria-hidden="true">
          <path d="M22 40 C16 36 13 30 13 25 C13 16 21 10 30 10 C39 10 47 16 47 25 C47 30 44 36 38 40 L38 46 L22 46 Z"/>
          <path d="M23 50 L37 50 M25 54 L35 54"/>
          <path d="M24 22 C24 18 28 16 30 18 C32 16 36 18 36 22 C38 24 37 28 34 29 C33 32 27 32 26 29 C23 28 22 24 24 22 Z M30 18 L30 32"/>
          <path d="M30 3 L30 6 M8 25 L4 25 M52 25 L56 25 M14 10 L11 7 M46 10 L49 7 M12 38 L9 40 M48 38 L51 40"/>
        </svg>
      </div>
      <h3 class="value-name">Thinking</h3>
      <div class="value-rule"></div>
      <p class="value-text">We believe in the power of thinking. Our rigorous and creative processes create beautifully considered solutions for our purchasers, the communities we develop within and the environment.</p>
    </article>

    <article class="value-card">
      <div class="value-badge">
        <svg viewBox="0 0 60 60" aria-hidden="true">
          <circle cx="30" cy="22" r="7"/>
          <circle cx="15" cy="26" r="5.5"/>
          <circle cx="45" cy="26" r="5.5"/>
          <path d="M17 46 C17 36 23 31 30 31 C37 31 43 36 43 46"/>
          <path d="M3 44 C3 37 8 33 14 33 C16 33 18 34 19 35"/>
          <path d="M57 44 C57 37 52 33 46 33 C44 33 42 34 41 35"/>
        </svg>
      </div>
      <h3 class="value-name">Team</h3>
      <div class="value-rule"></div>
      <p class="value-text">Property development is a team sport. We surround ourselves with the best designers and advisers. We strive to create an environment that allows them to do their best work and love doing it.</p>
    </article>

    <article class="value-card">
      <div class="value-badge">
        <svg viewBox="0 0 60 60" aria-hidden="true">
          <path d="M30 34 C24 29 19 25 19 20 C19 16 22 14 25 14 C27 14 29 15 30 17 C31 15 33 14 35 14 C38 14 41 16 41 20 C41 25 36 29 30 34 Z"/>
          <path d="M14 21 L23 21 L26 17 L29 24 L32 18 L34 21 L46 21"/>
          <path d="M8 28 L16 40 L24 46 L24 54"/>
          <path d="M52 28 L44 40 L36 46 L36 54"/>
        </svg>
      </div>
      <h3 class="value-name">Zoe</h3>
      <div class="value-rule"></div>
      <p class="value-text">Our mission is to create places for ‘Zoe’ - the Greek word for abundant life. We do this through exquisite design, quality construction and celebrating nature.</p>
    </article>
  </section>

  <footer class="footer">
    <span class="brand-name">VALDINTOR</span>
  </footer>
</main>
</body>
</html>
```